Coastal Learner Bureau business cards

Australian company about to start offering its services. We recruit international students to come to study English, vocational education and postgraduate courses in Australia. We help them find the institution and select the right city they want to come to Australia. We are a young, online oriented and supportive agency. Our clients are between 18 and 35 years old, mainly University students, young professionals or people with work experience. We provide much more information that any other agency offer. We administrate a Facebook group with more than 11.000 members that daily ask questions about general information when coming to Australia, while they are here and even after they leave the country

Target Market(s)

International students from South America, Central America and Europe

Industry/Entity Type

Student

Contact Information for Business Card

Tomas Bilbrea
Managing Director
tomas@kelvarin.com.au
www.kelvoria.com.au
+61 491058264
Melbourne, Australia

Font styles to use
Serif
Sans Serif

Colors

Designer to choose colors to be used in the design.

Requirements
Must have
• Horizontal design
• Standard business card size and shape. If font uses green or yellow colours, they will have to match the ones from the logo
Nice to have
• UPDATE: Use the contents of the green image to design one of the card sides. Use our logo in the background of that side as watermark.
• Passport image, or immigration stamps. A picture of the Yarra River (from Melbourne) would be cool as well.
Should not have
• Non-standard business card size and shape
• Not black as the background colour of any sides as we are not a VIP agency or a hight class service. We are orientes to young people and they like colours, pictures, something attractive.
• Vertical design
• NO YELLOW or BLACK AS THE BACKGROUND COLOUR OF ANY SIDE OF THE BIZ CARD

```html
<!DOCTYPE html>
<html lang="en">
<head>
<meta charset="utf-8">
<title>Coastal Learner Bureau – Business Cards</title>
<link rel="stylesheet" href="https://fonts.googleapis.com/css2?family=Roboto+Condensed:wght@500&family=Roboto:wght@400;500&display=swap">
<style>
  :root {
    --backdrop: #2b2b2b;
    --brand-green: #0f5c3e;
    --brand-yellow: #d6ad17;
    --paper: #f1f1f1;
    --ink-light: #ffffff;
  }
  * { box-sizing: border-box; margin: 0; padding: 0; }
  html, body {
    width: 1200px; height: 960px; overflow: hidden;
    background: var(--backdrop);
    font-family: "Roboto", Arial, sans-serif;
  }
  .canvas { position: relative; width: 1200px; height: 960px; }

  .card {
    position: absolute; width: 600px; height: 343px; overflow: hidden;
    box-shadow: 0 3px 8px rgba(0,0,0,0.45);
  }

  /* Front */
  .card-front { left: 314px; top: 113px; display: flex; }
  .contact-panel {
    width: 284px; height: 100%; background: var(--brand-green);
    padding: 96px 0 0 41px; color: var(--ink-light);
  }
  .person-name {
    font-family: "Roboto Condensed", "Arial Narrow", sans-serif;
    font-weight: 500; font-size: 23px; line-height: 26px;
    color: var(--brand-yellow); letter-spacing: 0.2px;
  }
  .person-role { font-weight: 500; font-size: 15px; line-height: 18px; margin-top: 1px; letter-spacing: 0.3px; }
  .person-city { font-size: 15px; line-height: 18px; margin-top: 22px; }
  .contact-list { list-style: none; margin-top: 11px; }
  .contact-list li {
    display: flex; align-items: center; gap: 8px;
    font-size: 15px; line-height: 19px;
  }
  .contact-icon { width: 14px; height: 14px; flex: none; }

  .brand-panel {
    flex: 1; height: 100%; background: var(--paper);
    display: flex; align-items: center; justify-content: center;
  }
  .brand-stripe { width: 13px; height: 100%; background: var(--brand-yellow); }

  .brand-name {
    display: flex; align-items: center; gap: 10px;
    font-weight: 500; font-size: 26px; line-height: 30px; text-align: left;
  }
  .brand-name-front { color: var(--brand-green); }
  .brand-name-back { color: var(--ink-light); font-size: 34px; line-height: 38px; }
  .brand-dot { flex: none; border-radius: 50%; background: var(--brand-yellow); }
  .brand-name-front .brand-dot { width: 14px; height: 14px; }
  .brand-name-back .brand-dot { width: 18px; height: 18px; }

  /* Back */
  .card-back {
    left: 311px; top: 472px; background: var(--brand-green);
  }
  .back-brand {
    position: absolute; left: 0; right: 0; top: 80px; height: 160px;
    display: flex; align-items: center; justify-content: center;
  }
  .tagline-band {
    position: absolute; left: 0; right: 0; top: 293px; height: 30px;
    background: var(--brand-yellow); color: var(--ink-light);
    font-size: 15px; line-height: 30px; text-align: center;
  }
</style>
</head>
<body>
<main class="canvas">

  <section class="card card-front" aria-label="Business card front">
    <div class="contact-panel">
      <h1 class="person-name">TOMAS BILBREA</h1>
      <p class="person-role">MANAGING DIRECTOR</p>
      <p class="person-city">Melbourne, Australia</p>
      <ul class="contact-list">
        <li>
          <svg class="contact-icon" viewBox="0 0 14 14" aria-hidden="true">
            <path fill="#d6ad17" d="M3 1.2l2 2.4-1.1 1.5c.8 1.7 2.2 3.1 3.9 3.9l1.5-1.1 2.4 2-1.2 2.2C5.8 12.1 1.9 8.2 1 3.3z"/>
          </svg>
          <span>+61 491058264</span>
        </li>
        <li>
          <svg class="contact-icon" viewBox="0 0 14 14" aria-hidden="true">
            <rect x="1" y="3" width="12" height="8.5" fill="#d6ad17"/>
            <path d="M1.3 3.4L7 7.6l5.7-4.2" fill="none" stroke="#0f5c3e" stroke-width="1.1"/>
          </svg>
          <span>tomas@kelvarin.com.au</span>
        </li>
        <li>
          <svg class="contact-icon" viewBox="0 0 14 14" aria-hidden="true">
            <circle cx="7" cy="7" r="6" fill="#d6ad17"/>
            <ellipse cx="7" cy="7" rx="2.4" ry="6" fill="none" stroke="#0f5c3e" stroke-width="1"/>
            <path d="M1 7h12" stroke="#0f5c3e" stroke-width="1"/>
          </svg>
          <span>www.kelvoria.com.au</span>
        </li>
      </ul>
    </div>
    <div class="brand-panel">
      <p class="brand-name brand-name-front"><span class="brand-dot" aria-hidden="true"></span><span>Coastal Learner<br>Bureau</span></p>
    </div>
    <div class="brand-stripe" aria-hidden="true"></div>
  </section>

  <section class="card card-back" aria-label="Business card back">
    <div class="back-brand">
      <p class="brand-name brand-name-back"><span class="brand-dot" aria-hidden="true"></span><span>Coastal Learner<br>Bureau</span></p>
    </div>
    <p class="tagline-band">Hacemos más por ti!</p>
  </section>

</main>
</body>
</html>
```